Design a "healthy, happy dog and cat" cheque/check background

I am looking for a few design concepts featuring a happy healthy dog and cat, that will be used as the background of a paper cheque/check.

This will require Photoshop and stock photos.

Here is the design brief: https://docs.plinvaro.com/document/d/4Rt8mKx2LqW9zVbN3cHy7TfJ1sDp6GaE0uYoZiXeMwnB/edit?usp=sharing

Colors

Designer to choose colors to be used in the design.

Requirements
Must have
• A happy dog and cat the main focus within the "empty" central part of the cheque/check, and a complementary background for the rest of the cheque, following the design guidelines in the attached plinvaro doc.

```html
<!DOCTYPE html>
<html lang="en">
<head>
<meta charset="utf-8">
<title>Personal Cheque – Dog Background</title>
<link rel="stylesheet" href="https://fonts.googleapis.com/css2?family=Arimo:wght@400;700&family=Share+Tech+Mono&display=swap">
<style>
  :root {
    --page: #ffffff;
    --ink: #2e2e2e;
    --ink-soft: #3c3c3c;
    --fur-light: #a39288;
    --fur-mid: #8a786d;
    --fur-dark: #5f4c42;
    --blanket: #c9c7c3;
    --blanket-dark: #9a9895;
    --veil: rgba(255, 255, 255, 0.28);
    --field: #ffffff;
    --rule: #4a4a4a;
  }
  * { margin: 0; padding: 0; box-sizing: border-box; }
  html, body { width: 1200px; height: 544px; overflow: hidden; background: var(--page); }
  body { position: relative; font-family: "Arimo", Arial, sans-serif; color: var(--ink); }

  .cheque { position: absolute; left: 24px; top: 20px; width: 1168px; height: 388px; overflow: hidden; }
  .cheque-photo {
    position: absolute; inset: 0;
    background:
      radial-gradient(ellipse 38% 55% at 88% 78%, var(--blanket) 0%, var(--blanket-dark) 60%, transparent 100%),
      radial-gradient(ellipse 30% 45% at 58% 95%, var(--blanket) 0%, transparent 100%),
      linear-gradient(100deg, var(--fur-light) 0%, var(--fur-mid) 35%, var(--fur-dark) 62%, var(--fur-mid) 78%, var(--blanket-dark) 100%);
  }
  .cheque-photo::after { content: ""; position: absolute; inset: 0; background: var(--veil); }

  .abs { position: absolute; white-space: nowrap; }

  .account-name { left: 34px; top: 56px; font-size: 22px; font-weight: 700; color: var(--ink-soft); }
  .account-address { left: 34px; top: 84px; font-size: 19px; line-height: 22px; color: var(--ink-soft); }
  .cheque-number { left: 1000px; top: 36px; font-size: 24px; font-weight: 700; color: #111; }

  .date-label { left: 760px; top: 108px; font-size: 20px; color: var(--ink); }
  .date-boxes { left: 824px; top: 70px; display: flex; gap: 2.5px; }
  .date-box { width: 36.5px; text-align: center; }
  .date-box .cell { height: 36px; background: var(--field); }
  .date-box .hint { font-size: 14px; margin-top: 6px; color: var(--ink); }

  .payee-label { left: 32px; top: 170px; font-size: 14px; line-height: 14px; color: var(--ink); }
  .dollar-sign { left: 922px; top: 166px; font-size: 32px; color: var(--ink); }
  .amount-box { left: 948px; top: 154px; width: 194px; height: 48px; background: var(--field); }
  .amount-words { left: 894px; top: 228px; font-size: 15px; color: var(--ink); }

  .bank-mark { left: 34px; top: 270px; width: 72px; height: 72px; border-radius: 50%; background: #1c1c1c; }
  .bank-name { left: 130px; top: 279px; font-size: 19px; font-weight: 700; color: #111; }
  .bank-address { left: 130px; top: 300px; font-size: 18px; line-height: 19px; color: #111; letter-spacing: 0.4px; }
  .company-name { left: 786px; top: 313px; font-size: 15px; color: #111; }
  .memo-label { left: 37px; top: 362px; font-size: 12px; color: #111; }

  .security-badge { left: 1138px; top: 252px; width: 28px; height: 132px; border: 1px solid #666; border-radius: 3px; background: rgba(255,255,255,0.35); }

  .cheque-lines { position: absolute; inset: 0; }

  .micr-line { left: 53px; top: 446px; font-family: "Share Tech Mono", monospace; font-size: 30px; letter-spacing: 3px; color: #111; }
</style>
</head>
<body>
  <section class="cheque" aria-label="Personal cheque">
    <div class="cheque-photo" role="img" aria-label="Background photograph of a brown long-haired dog resting on a knitted grey blanket"></div>

    <svg class="cheque-lines" width="1168" height="388" viewBox="0 0 1168 388" aria-hidden="true">
      <g fill="none" stroke="var(--rule)" stroke-width="1.4">
        <polyline points="32,202 900,202 900,172"/>
        <polyline points="32,256 882,256 890,222"/>
        <line x1="32" y1="376" x2="564" y2="376"/>
        <line x1="661" y1="376" x2="1074" y2="376"/>
      </g>
    </svg>

    <div class="abs account-name">Northvale Cheques Personal Cheque</div>
    <div class="abs account-address">15 Residential Street<br>Toronto, Ontario M1M 1M1</div>
    <div class="abs cheque-number">101</div>

    <div class="abs date-label">DATE</div>
    <div class="abs date-boxes">
      <div class="date-box"><div class="cell"></div><div class="hint">D</div></div>
      <div class="date-box"><div class="cell"></div><div class="hint">D</div></div>
      <div class="date-box"><div class="cell"></div><div class="hint">M</div></div>
      <div class="date-box"><div class="cell"></div><div class="hint">M</div></div>
      <div class="date-box"><div class="cell"></div><div class="hint">Y</div></div>
      <div class="date-box"><div class="cell"></div><div class="hint">Y</div></div>
      <div class="date-box"><div class="cell"></div><div class="hint">Y</div></div>
      <div class="date-box"><div class="cell"></div><div class="hint">Y</div></div>
    </div>

    <div class="abs payee-label">PAY TO THE<br>ORDER OF</div>
    <div class="abs dollar-sign">$</div>
    <div class="abs amount-box"></div>
    <div class="abs amount-words">100 DOLLARS</div>

    <div class="abs bank-mark" aria-hidden="true"></div>
    <div class="abs bank-name">Your Financial Institution</div>
    <div class="abs bank-address">200 Finance Avenue<br>Your City, Your Province A1B 2CS</div>
    <div class="abs company-name">Optional Company Name</div>
    <div class="abs memo-label">MEMO</div>

    <div class="abs security-badge" aria-hidden="true"></div>
  </section>

  <div class="abs micr-line">⑈101⑈ ⑆12345⑉678⑆ 12345⑉6789⑈</div>
</body>
</html>
```